Looking for a dynamic business card for a pizzeria.

A business card with our food, logo, and space for name, title, email, website, phone. The card should convey quality, unique, amazing. On the front, I envision food photo or photos with the owners names and contact information. On the back, more food with locations, website, facebook, twitter, instagram icons. It should look polished, not cartoonish, or plain.
Target Market(s)
upscale, local food buyers, 30-50 years in age.
Industry/Entity Type
Restaurant
Contact Information for Business Card
Business Name: Bru'nettix, LLC
Website: www.brunettix.com
Back:
2 locations: (can list on the back of card)
1. Harborside
4087 Corlan Avenue
Cedarbrook, WA 98471
360-481-5067
2. Crestview Hill
7315 Wendmere Road
Cedarbrook, WA 98476
360-293-8840
front:
EDITABLE space for
Business name
Person's Name
title
2nd title
Email address
cell-phone number
Requirements
Must have
- logo
- my food photo or photos (no watermarks showing)
- locations on back
- Person contact information on front
- full bleed

```html
<!DOCTYPE html>
<html lang="en">
<head>
<meta charset="utf-8">
<title>Bru'nettix Business Card</title>
<link href="https://fonts.googleapis.com/css2?family=Questrial&family=Didact+Gothic&display=swap" rel="stylesheet">
<style>
  :root {
    --card-red: #c23b3e;
    --card-white: #f2f2f0;
    --brand-green: #2e7a3c;
    --brand-red: #c8343a;
    --ink: #2b2b2b;
    --ink-soft: #555;
    --paper: #ffffff;
    --stage: #e7e4df;
  }
  * { box-sizing: border-box; margin: 0; padding: 0; }
  html, body { width: 1200px; height: 900px; overflow: hidden; }
  body {
    background: var(--stage);
    font-family: "Questrial", "Didact Gothic", sans-serif;
    position: relative;
  }
  .card {
    position: absolute;
    left: 250px;
    width: 700px;
    height: 400px;
    overflow: hidden;
    box-shadow: 0 6px 18px rgba(0,0,0,0.18);
  }
  /* Back side: locations */
  .card--back { top: 40px; background: var(--card-red); color: var(--paper); }
  .locations {
    position: absolute; left: 48px; top: 50px;
    font-size: 21px; line-height: 1.38;
  }
  .location__name { font-weight: 700; letter-spacing: 0.3px; }
  .location + .location { margin-top: 4px; }
  .food-collage { position: absolute; right: 0; top: 0; width: 380px; height: 400px; }
  .follow {
    position: absolute; right: 36px; bottom: 24px;
    display: flex; align-items: center; gap: 10px;
  }
  .follow__label {
    font-size: 14px; font-weight: 700; letter-spacing: 0.5px;
    text-transform: uppercase; margin-right: 6px;
  }
  .follow__dot { width: 22px; height: 22px; border-radius: 50%; background: var(--paper); }

  /* Front side: contact */
  .card--front { top: 470px; background: var(--card-white); color: var(--ink); }
  .contact {
    position: absolute; left: 48px; top: 54px;
    font-size: 14px; line-height: 1.8; color: var(--ink-soft);
  }
  .contact__name { font-weight: 700; color: var(--ink); }
  .brand {
    position: absolute; right: 56px; top: 158px;
    display: flex; align-items: center; gap: 16px;
  }
  .brand__name {
    font-size: 54px; color: var(--brand-green); letter-spacing: 1px; line-height: 1;
  }
  .brand__mark { width: 72px; height: 72px; border-radius: 50%; background: var(--brand-red); flex: none; }
</style>
</head>
<body>

<section class="card card--back" aria-label="Card back with locations">
  <div class="locations">
    <div class="location">
      <div class="location__name">Harborside</div>
      <div>4087 Corlan Avenue</div>
      <div>Cedarbrook, WA 98471</div>
      <div>360-481-5067</div>
    </div>
    <div class="location">
      <div class="location__name">Crestview Hill</div>
      <div>7315 Wendmere Road</div>
      <div>Cedarbrook, WA 98476</div>
      <div>360-293-8840</div>
    </div>
  </div>

  <svg class="food-collage" viewBox="0 0 380 400">
    <defs>
      <radialGradient id="g-pepperoni" cx="50%" cy="50%" r="60%">
        <stop offset="0" stop-color="#e9a48e"/><stop offset="1" stop-color="#b5503c"/>
      </radialGradient>
      <radialGradient id="g-dough" cx="50%" cy="50%" r="60%">
        <stop offset="0" stop-color="#e8cfa6"/><stop offset="1" stop-color="#8a7a6a"/>
      </radialGradient>
      <radialGradient id="g-sandwich" cx="50%" cy="50%" r="60%">
        <stop offset="0" stop-color="#d9b466"/><stop offset="1" stop-color="#6f8a3e"/>
      </radialGradient>
      <radialGradient id="g-oven" cx="50%" cy="40%" r="65%">
        <stop offset="0" stop-color="#f0a048"/><stop offset="1" stop-color="#8f3a22"/>
      </radialGradient>
    </defs>
    <circle cx="120" cy="95" r="95" fill="url(#g-pepperoni)" role="img" aria-label="Photo: hands topping a pepperoni pizza"/>
    <circle cx="290" cy="150" r="90" fill="url(#g-dough)" role="img" aria-label="Photo: hands shaping pizza dough"/>
    <circle cx="90" cy="280" r="90" fill="url(#g-sandwich)" role="img" aria-label="Photo: toasted sandwich with greens"/>
    <circle cx="270" cy="310" r="95" fill="url(#g-oven)" role="img" aria-label="Photo: pepperoni rolls on a tray by the oven"/>
  </svg>

  <div class="follow">
    <span class="follow__label">Follow us on</span>
    <span class="follow__dot"></span><span class="follow__dot"></span>
    <span class="follow__dot"></span><span class="follow__dot"></span>
    <span class="follow__dot"></span><span class="follow__dot"></span>
    <span class="follow__dot"></span><span class="follow__dot"></span>
  </div>
</section>

<section class="card card--front" aria-label="Card front with contact">
  <div class="contact">
    <div><span class="contact__name">Marcel Dufresne</span> Marketing</div>
    <div>marcel@saveurstudio.com</div>
    <div>819-555-2140 cell</div>
    <div>1-888-555-0193</div>
    <div>819-555-2276</div>
    <div>www.saveurstudio.com</div>
  </div>
  <div class="brand">
    <span class="brand__name">Bru'nettix</span>
    <span class="brand__mark"></span>
  </div>
</section>

</body>
</html>
```